Business card for law firm

Need business card for new law firm. Think confident, authoritative, conservative, but not stuffy or old-fashioned.

Contact Information for Business Card

Content for card - logo (uploaded), plus the following:

Paul Whitcombe (larger font)
Managing Partner (larger font, but not as large as name)
Level 9, 7 Ferris Lane
Sydney NSW 2000
Main Tel 02 9364 2710
Direct Tel 02 8472 3159
Email paul@qvlegal.com.au
www.qvlegal.com.au

Letterhead design should include logo plus:
Level 9, 7 Ferris Lane
Sydney NSW 2000
Tel 02 8472 3159
www.qvlegal.com.au

```html
<!DOCTYPE html>
<html lang="en">
<head>
<meta charset="utf-8">
<title>Quayvale Lawyers – Business Card</title>
<link rel="stylesheet" href="https://fonts.googleapis.com/css2?family=Open+Sans:wght@400;600;700&display=swap">
<style>
  :root {
    --navy: #0f1f5c;
    --ink-grey: #555a60;
    --soft-grey: #6d7177;
    --card: #ffffff;
    --backdrop: #3b3e42;
  }
  * { box-sizing: border-box; margin: 0; padding: 0; }
  html, body {
    width: 1200px;
    height: 1000px;
    overflow: hidden;
    background: var(--backdrop);
    font-family: "Open Sans", Arial, sans-serif;
  }
  .stage {
    position: relative;
    width: 1200px;
    height: 1000px;
  }
  .card {
    position: absolute;
    left: 220px;
    width: 760px;
    height: 434px;
    background: var(--card);
    box-shadow: 0 10px 30px rgba(0,0,0,0.35);
    overflow: hidden;
  }
  .card--back { top: 50px; }
  .card--front { top: 516px; }

  /* Back */
  .brand {
    position: absolute;
    left: 0; right: 0;
    top: 150px;
    display: flex;
    align-items: center;
    justify-content: center;
    gap: 16px;
  }
  .brand-mark {
    width: 36px;
    height: 36px;
    background: var(--navy);
  }
  .brand-name {
    color: var(--navy);
    font-weight: 600;
    font-size: 40px;
    letter-spacing: 3px;
    text-transform: uppercase;
  }
  .web {
    position: absolute;
    left: 0; right: 0;
    top: 262px;
    text-align: center;
    color: var(--soft-grey);
    font-size: 19px;
    letter-spacing: 5px;
  }

  /* Front */
  .person {
    position: absolute;
    left: 58px;
    top: 150px;
  }
  .person-name {
    color: var(--navy);
    font-weight: 700;
    font-size: 27px;
    line-height: 1.05;
    text-transform: uppercase;
  }
  .person-title {
    color: var(--ink-grey);
    font-weight: 700;
    font-size: 17px;
    text-transform: uppercase;
    margin-bottom: 8px;
  }
  .contact-list { list-style: none; }
  .contact-item {
    display: flex;
    align-items: center;
    gap: 12px;
    color: var(--ink-grey);
    font-size: 17px;
    line-height: 1.4;
  }
  .contact-icon { width: 16px; height: 16px; fill: var(--navy); flex: none; }
  .address-band {
    position: absolute;
    left: 0; right: 0;
    top: 318px;
    height: 54px;
    background: var(--navy);
    color: #ffffff;
    font-size: 18px;
    display: flex;
    align-items: center;
    padding-left: 40px;
  }
  .front-mark {
    position: absolute;
    right: 70px;
    top: 90px;
    width: 170px;
    height: 170px;
    background: var(--navy);
  }
</style>
</head>
<body>
<main class="stage">
  <section class="card card--back" aria-label="Card back">
    <div class="brand">
      <span class="brand-mark"></span>
      <span class="brand-name">Quayvale Lawyers</span>
    </div>
    <p class="web">www.qvlegal.com.au</p>
  </section>

  <section class="card card--front" aria-label="Card front">
    <div class="person">
      <h1 class="person-name">Paul Whitcombe</h1>
      <p class="person-title">Managing Partner</p>
      <ul class="contact-list">
        <li class="contact-item">
          <svg class="contact-icon" viewBox="0 0 16 16" aria-hidden="true"><path d="M1 5c0-2 3-3 7-3s7 1 7 3v1.5h-3.5V5h-7v1.5H1z"/><path d="M3 8h10l1 6H2z"/></svg>
          02 9364 2710
        </li>
        <li class="contact-item">
          <svg class="contact-icon" viewBox="0 0 16 16" aria-hidden="true"><path d="M4 0h8a1 1 0 0 1 1 1v14a1 1 0 0 1-1 1H4a1 1 0 0 1-1-1V1a1 1 0 0 1 1-1zm1 2v10h6V2z"/></svg>
          02 8472 3159
        </li>
        <li class="contact-item">
          <svg class="contact-icon" viewBox="0 0 16 16" aria-hidden="true"><path d="M0 3h16v1L8 9 0 4z"/><path d="M0 5.5l8 5 8-5V13H0z"/></svg>
          paul@qvlegal.com.au
        </li>
      </ul>
    </div>
    <div class="address-band">Level 9, 7 Ferris Lane Sydney NSW 2000</div>
    <div class="front-mark" aria-hidden="true"></div>
  </section>
</main>
</body>
</html>
```